Website re-design and completion for www.brovimark.com

Graphically redesign and complete the existing site www.brovimark.com
This site intent is to:
a) introduce and educate about a new Technoloy to customers in a variety of different industries using traditional methods.
b) outline and promote the benefits and ROI of using the new techology
c) Sell our machines by showing customers the benefits and reasons to purchase from us over other suppliers
We do want to keep the overall concept. Like the home page with a slider. The most important thing to us is to increase the design of the slider. Next we need it standard layout with some attractive design to describe each product group. There are 3 product groups. Laser Cleaning Machines, Laser Welding Machines and Laser Cutting Machines

Target Market(s)

Mostly business to business.

Coding

Coded - Design and coding required

Font styles to use
Sans Serif
Other font styles liked:
• Calibri, Arial

Requirements
Must have
• A serious approach as we are targeting professionals, such as production managers, engineers and so forth
Should not have
• Annoying call to action stuff. Overly playful gimmicks.

```html
<!DOCTYPE html>
<html lang="en">
<head>
<meta charset="utf-8">
<title>Brovimark Laser</title>
<link href="https://fonts.googleapis.com/css2?family=Audiowide&family=Lato:wght@400;700&display=swap" rel="stylesheet">
<style>
:root{
  --blue:#0a7fc9;
  --red:#c0202e;
  --red-deep:#a91c29;
  --navy:#0b1838;
  --ink:#1a1a1a;
  --text:#444;
  --white:#fff;
  --black:#000;
}
*{margin:0;padding:0;box-sizing:border-box}
html,body{width:1200px;height:3446px;overflow:hidden}
body{font-family:'Lato',Arial,sans-serif;color:var(--ink);background:var(--white);position:relative}
.display{font-family:'Audiowide','Lato',sans-serif;font-weight:400;letter-spacing:1px}
section,header,footer{position:absolute;left:0;width:1200px}
.abs{position:absolute}

/* header */
.site-header{top:0;height:139px;border-top:5px solid var(--blue);background:var(--white)}
.brand{left:111px;top:38px;font-size:38px;color:var(--red);font-weight:700;letter-spacing:1px}
.contact-chip{top:18px;display:flex;gap:16px;align-items:flex-start}
.chip-icon{width:48px;height:48px;border-radius:50%;background:var(--red);display:flex;align-items:center;justify-content:center}
.chip-label{color:var(--red);font-size:15px;margin-top:4px}
.chip-value{color:#222;font-size:16px;margin-top:6px}
.main-nav{top:99px;font-size:15.5px;color:#333}
.main-nav a{position:absolute;white-space:nowrap;color:#333;text-decoration:none}
.main-nav a.active{color:var(--blue);font-weight:700}

/* hero */
.hero{top:139px;height:599px;overflow:hidden}
.hero-photo{position:absolute;inset:0;background:
  radial-gradient(circle at 72% 58%, rgba(255,214,140,.85) 0, rgba(220,150,70,.35) 8%, rgba(40,60,120,0) 22%),
  radial-gradient(ellipse at 78% 25%, #4b5c86 0, rgba(40,55,95,.6) 20%, rgba(11,24,56,0) 45%),
  linear-gradient(90deg,#0b1838 0,#14244c 55%,#1e2c52 100%)}
.hero-title{left:111px;top:116px;color:var(--white);font-size:64px;line-height:77px}
.hero-lead{left:111px;top:297px;width:540px;color:var(--white);font-size:20.5px;line-height:31px}
.btn{position:absolute;display:flex;align-items:center;justify-content:center;font-size:15px;font-weight:700;text-decoration:none}
.btn-light{left:111px;top:430px;width:154px;height:37px;background:var(--white);color:var(--red)}
.btn-red{width:154px;height:37px;background:var(--red);color:var(--white)}

/* products */
.products{top:738px;height:710px;background:var(--white)}
.section-title{position:absolute;left:0;width:1200px;text-align:center;font-size:44px}
.products .section-title{top:75px;color:var(--ink)}
.accent{color:var(--blue)}
.tab{position:absolute;top:170px;width:231px;height:55px;border:2px solid var(--blue);color:var(--blue);font-size:22px;font-weight:700;display:flex;align-items:center;justify-content:center}
.tab.active{background:var(--blue);color:var(--white)}
.product-card{position:absolute;top:291px;width:300px}
.product-photo{height:273px}
.product-card h3{margin-top:32px;text-align:center;font-size:26px;font-weight:700;color:var(--ink)}
.ph-rust{background:linear-gradient(135deg,#8a7f74,#5d4a3a 45%,#b8b0a6)}
.ph-paint{background:linear-gradient(160deg,#6f6c68,#2f2d2b 55%,#8f8a84)}
.ph-parts{background:linear-gradient(135deg,#d8cab0,#8c7f70 50%,#4a4642)}
.slide-arrow{position:absolute;width:38px;height:38px}

/* benefits */
.benefits{top:1448px;height:535px;overflow:hidden}
.benefits-photo{position:absolute;inset:0;background:
  radial-gradient(ellipse at 66% 30%, rgba(240,170,170,.45) 0, rgba(184,34,47,0) 40%),
  linear-gradient(180deg,#b8222f,#b52634 60%,#ae1f2c)}
.benefits .section-title{top:88px;color:var(--white);font-size:42px}
.benefit{position:absolute;top:165px;width:290px;text-align:center;color:var(--white)}
.benefit-icon{width:75px;height:75px;border-radius:50%;background:var(--white);margin:0 auto;display:flex;align-items:center;justify-content:center}
.benefit h3{margin-top:18px;font-size:21.5px;font-weight:700}
.benefit p{margin-top:14px;font-size:15px;line-height:25.7px}
.benefit .more{margin-top:12px;height:20px}

/* about */
.about{top:1983px;height:661px;background:var(--white)}
.about-photo-back{left:111px;top:87px;width:388px;height:357px;background:linear-gradient(135deg,#3b3b3b,#8e8a86 35%,#2d2d2d 70%,#5a5a5a)}
.about-photo-front{left:223px;top:254px;width:344px;height:319px;background:linear-gradient(160deg,#5c5a58,#9a9896 40%,#3a3836 80%);border:2px solid var(--white)}
.about h2{left:642px;top:92px;font-size:44px;color:var(--ink)}
.about-copy{left:642px;top:171px;width:448px;font-size:15.3px;line-height:25.6px;color:var(--text)}
.about-copy p+p{margin-top:28px}
.about .btn-red{left:643px;top:513px}

/* why */
.why{top:2644px;height:391px;overflow:hidden}
.why-photo{position:absolute;inset:0;background:
  radial-gradient(ellipse at 55% 70%, rgba(120,190,235,.45) 0, rgba(10,127,201,0) 45%),
  linear-gradient(180deg,#0a7fc9,#0b78bf)}
.why .section-title{top:68px;color:var(--white)}
.why-copy{left:135px;top:151px;width:930px;text-align:center;color:var(--white);font-size:15.3px;line-height:25.8px}
.why .btn-red{left:523px;top:276px}

/* footer */
.site-footer{top:3035px;height:411px;background:var(--black);color:var(--white)}
.partner-name{left:114px;top:98px;font-size:30px;font-weight:700;color:var(--blue);letter-spacing:1px}
.footer-about{left:114px;top:172px;width:250px;font-size:15.3px;line-height:25.8px}
.footer-col h4{font-size:21px;font-weight:700}
.footer-col ul{list-style:none;margin-top:19px}
.footer-col li{font-size:15.3px;line-height:30px}
.footer-contact li{line-height:34px}
.copyright{left:0;width:1200px;top:377px;text-align:center;font-size:13px}
</style>
</head>
<body>

<header class="site-header">
  <div class="abs brand">BROVIMARK LASER</div>

  <div class="abs contact-chip" style="left:694px">
    <div class="chip-icon">
      <svg width="22" height="22" viewBox="0 0 24 24"><path fill="#fff" d="M6.6 10.8a15.2 15.2 0 0 0 6.6 6.6l2.2-2.2a1 1 0 0 1 1-.25 11.4 11.4 0 0 0 3.6.6 1 1 0 0 1 1 1V20a1 1 0 0 1-1 1A17 17 0 0 1 3 4a1 1 0 0 1 1-1h3.5a1 1 0 0 1 1 1c0 1.25.2 2.45.6 3.6a1 1 0 0 1-.25 1z"/></svg>
    </div>
    <div><div class="chip-label">Call Us</div><div class="chip-value">555-014-2270</div></div>
  </div>

  <div class="abs contact-chip" style="left:892px">
    <div class="chip-icon">
      <svg width="22" height="22" viewBox="0 0 24 24"><path fill="#fff" d="M3 5h18a1 1 0 0 1 1 1v1.2l-10 6-10-6V6a1 1 0 0 1 1-1zm-1 4.6 10 6 10-6V18a1 1 0 0 1-1 1H3a1 1 0 0 1-1-1z"/></svg>
    </div>
    <div><div class="chip-label">Email</div><div class="chip-value">info@brovimark.com</div></div>
  </div>

  <nav class="abs main-nav" style="left:0">
    <a class="active" style="left:559px">Home</a>
    <a style="left:657px">About Us</a>
    <a style="left:776px">Products</a>
    <a style="left:897px">Services</a>
    <a style="left:1013px">Contact Us</a>
  </nav>
</header>

<section class="hero">
  <div class="hero-photo" role="img" aria-label="Laser cutting head throwing sparks onto sheet metal"></div>
  <h1 class="abs hero-title display">WELCOME<br>TO BROVIMARK LASER</h1>
  <p class="abs hero-lead">Lorem ipsum dolor sit amet, consectetur adipiscing elit, sed do eiusmod tempor incididunt ut labore et dolore magna aliqua.</p>
  <a class="btn btn-light">Contact Us</a>
</section>

<section class="products">
  <h2 class="section-title display">OUR <span class="accent">PRODUCTS</span></h2>
  <div class="tab active" style="left:113px">Laser Cleaning</div>
  <div class="tab" style="left:484px">Laser Welding</div>
  <div class="tab" style="left:855px">Laser Cutting</div>

  <svg class="slide-arrow" style="left:52px;top:408px" viewBox="0 0 40 40"><circle cx="20" cy="20" r="19" fill="#c0202e"/><path d="M22 11 13 20l9 9M13 20h15" stroke="#fff" stroke-width="4.5" fill="none" stroke-linecap="round" stroke-linejoin="round"/></svg>
  <svg class="slide-arrow" style="left:1108px;top:408px" viewBox="0 0 40 40"><circle cx="20" cy="20" r="19" fill="#c0202e"/><path d="M18 11l9 9-9 9M27 20H12" stroke="#fff" stroke-width="4.5" fill="none" stroke-linecap="round" stroke-linejoin="round"/></svg>

  <div class="product-card" style="left:111px">
    <div class="product-photo ph-rust" role="img" aria-label="Laser beam removing rust from a steel bar"></div>
    <h3>Rust Removal</h3>
  </div>
  <div class="product-card" style="left:449px">
    <div class="product-photo ph-paint" role="img" aria-label="Metal wheel hub with paint stripped by laser"></div>
    <h3>Paint Stripping</h3>
  </div>
  <div class="product-card" style="left:787px">
    <div class="product-photo ph-parts" role="img" aria-label="Laser cleaning a flywheel part"></div>
    <h3>Parts Cleaning</h3>
  </div>
</section>

<section class="benefits">
  <div class="benefits-photo" role="img" aria-label="Red-tinted laser cutting background"></div>
  <h2 class="section-title display">BENEFITS</h2>

  <svg class="slide-arrow" style="left:44px;top:298px" viewBox="0 0 40 40"><circle cx="20" cy="20" r="19" fill="#fff"/><path d="M22 11 13 20l9 9M13 20h15" stroke="#c0202e" stroke-width="4.5" fill="none" stroke-linecap="round" stroke-linejoin="round"/></svg>
  <svg class="slide-arrow" style="left:1117px;top:298px" viewBox="0 0 40 40"><circle cx="20" cy="20" r="19" fill="#fff"/><path d="M18 11l9 9-9 9M27 20H12" stroke="#c0202e" stroke-width="4.5" fill="none" stroke-linecap="round" stroke-linejoin="round"/></svg>

  <div class="benefit" style="left:88px">
    <div class="benefit-icon">
      <svg width="40" height="40" viewBox="0 0 40 40" fill="none" stroke="#c0202e" stroke-width="1.8"><rect x="9" y="6" width="22" height="28" rx="2"/><path d="M13 13l2 2 3-3M13 21l2 2 3-3M13 29l2 2 3-3M21 14h6M21 22h6M21 30h6"/></svg>
    </div>
    <h3>No Consumables Required</h3>
    <p>Laser cleaning does not require any consumables, such as sanding discs, blasting media, grinding discs or chemicals</p>
    <div class="more"><svg width="16" height="16" viewBox="0 0 16 16"><path d="M7 2l6 6-6 6M13 8H2" stroke="#fff" stroke-width="2.6" fill="none"/></svg></div>
  </div>

  <div class="benefit" style="left:454px">
    <div class="benefit-icon">
      <svg width="40" height="40" viewBox="0 0 40 40" fill="none" stroke="#c0202e" stroke-width="1.8"><path d="M20 22v-7M20 15c-5 0-7-4-7-8 4 0 7 3 7 8zM20 15c4 0 7-3 7-7-4 0-7 2-7 7z"/><path d="M6 28c4-3 8-4 12-2h6a2 2 0 0 1 0 4h-6M24 30l8-4a2 2 0 0 1 2 3l-9 6H12l-6-2"/></svg>
    </div>
    <h3>Environmentally Friendly</h3>
    <p>A superior alternative to methods like sandblasting or washing, as it eliminates the need for consumable chemicals and materials.</p>
    <div class="more"><svg width="16" height="16" viewBox="0 0 16 16"><path d="M7 2l6 6-6 6M13 8H2" stroke="#fff" stroke-width="2.6" fill="none"/></svg></div>
  </div>

  <div class="benefit" style="left:821px">
    <div class="benefit-icon">
      <svg width="40" height="40" viewBox="0 0 40 40" fill="none" stroke="#c0202e" stroke-width="1.8"><circle cx="16" cy="17" r="4"/><path d="M16 7v3M16 24v3M6 17h3M23 17h3M9 10l2 2M21 22l2 2M9 24l2-2M21 12l2-2"/><circle cx="28" cy="28" r="3"/><path d="M28 21v2M28 33v2M21 28h2M33 28h2"/></svg>
    </div>
    <h3>No Mechanical Contact</h3>
    <p>Laser cleaning and laser ablation is a non-contact form of cleaning. It means no physical impact to the materials.</p>
    <div class="more"><svg width="16" height="16" viewBox="0 0 16 16"><path d="M7 2l6 6-6 6M13 8H2" stroke="#fff" stroke-width="2.6" fill="none"/></svg></div>
  </div>
</section>

<section class="about">
  <div class="abs about-photo-back" role="img" aria-label="Laser cleaning flash on a metal surface"></div>
  <div class="abs about-photo-front" role="img" aria-label="Handheld laser welding gun joining steel plates"></div>
  <h2 class="abs display">ABOUT <span class="accent">US</span></h2>
  <div class="abs about-copy">
    <p>Lorem ipsum dolor sit amet, consectetur adipiscing elit, sed do eiusmod tempor incididunt ut labore et dolore magna aliqua. Ut enim ad minim veniam, quis nostrud exercitation ullamco laboris nisi ut aliquip ex ea commodo consequat.</p>
    <p>Duis aute irure dolor in reprehenderit in voluptate velit esse cillum dolore eu fugiat nulla pariatur. Excepteur sint occaecat cupidatat non proident, sunt in culpa qui officia deserunt mollit anim id est laborum. Sed ut perspiciatis unde omnis iste natus error sit voluptatem accusantium doloremque laudantium, totam rem aperiam, eaque ipsa quae ab illo inventore veritatis et quasi architecto beatae vitae dicta sunt explicabo.</p>
  </div>
  <a class="btn btn-red">Read More</a>
</section>

<section class="why">
  <div class="why-photo" role="img" aria-label="Blue-tinted sparks from laser cutting"></div>
  <h2 class="section-title display">WHY BROVIMARK LASER?</h2>
  <p class="abs why-copy">At Brovimark Laser, we're dedicated to providing you with top-of-the-line equipment that you can rely on for all your manufacturing requirements. With years of expertise in the manufacturing industry, we understand the importance of laser photonics equipment and the myriad questions that may arise when integrating laser technology into your operations. That's why we're here to offer comprehensive support and guidance every step of the way.</p>
  <a class="btn btn-red">Read More</a>
</section>

<footer class="site-footer">
  <div class="abs partner-name">NORVANE</div>
  <p class="abs footer-about">Brovimark Laser is an authorized service center, stocking center, and parts distributor for NORVANE OPTICS products.</p>

  <div class="abs footer-col" style="left:570px;top:91px">
    <h4>Links</h4>
    <ul><li>Home</li><li>About Us</li><li>Products</li><li>Services</li><li>Contact Us</li></ul>
  </div>

  <div class="abs footer-col footer-contact" style="left:904px;top:91px">
    <h4>Contact Us</h4>
    <ul><li>Email:&nbsp; info@brovimark.com</li><li>Phone:&nbsp; 555-014-2270</li><li>Location:&nbsp; Lakeview, IL 60000</li></ul>
  </div>

  <p class="abs copyright">Copyright © 2024 Brovimark Laser, LLC. All Rights Reserved.</p>
</footer>

</body>
</html>
```